Construction material supplies company business card ****

1. Full company name “K T Masonry Works Ltd”
I am after a Business card design for the company as a whole. We are better known in Solomon Islands as “K T Masonry” for short.

We are a building materials supplier of
Ready Mixed Concrete, Bricks and Blocks,
Quarry products- gravel, aggregates, sand etc.
Cement distributor/retailer of reputable brands.
Other prefab concrete products. Culverts, wave breakers, concrete retaining blocks etc.

2. Competitive Advantage over Competition: Quality, efficient, professional, dependable, reliable

3. We want people to feel trust worthy, high quality, strong when they see our brand

5. No preference to color. Maybe more sturdy and corporate. Not fancy.

Industry/Entity Type

CONSTRUCTION SUPPLY

Contact Information for Business Card

Name, Position, office phone mob phone, email

Requirements
Must have
• the company logo
Nice to have
• would like to see a mixture of designs, of with logo only and also with simple graphic designs to bring out the company whilst still have the strong sturdy professional feeling

```html
<!DOCTYPE html>
<html lang="en">
<head>
<meta charset="utf-8">
<title>K T Masonry — Business Card</title>
<link href="https://fonts.googleapis.com/css2?family=Orbitron:wght@700&family=Poppins:wght@400;500&display=swap" rel="stylesheet">
<style>
  :root {
    --navy: #1d4a7a;
    --navy-dark: #13365d;
    --accent: #3f8fd6;
    --concrete-1: #eef0f2;
    --concrete-2: #d4d8dc;
    --white: #ffffff;
    --page: #e6e7e9;
  }
  html, body {
    margin: 0; padding: 0;
    width: 1200px; height: 900px;
    overflow: hidden;
    background: var(--page);
  }
  .canvas {
    position: relative;
    width: 1200px; height: 900px;
  }
  .card {
    position: absolute;
    left: 190px;
    width: 820px; height: 400px;
    border-radius: 26px;
    overflow: hidden;
    box-shadow: 0 8px 24px rgba(0,0,0,.18);
    background: radial-gradient(ellipse at 30% 30%, var(--concrete-1), var(--concrete-2) 90%);
  }
  .card--back { top: 40px; }
  .card--front { top: 460px; }

  .brand {
    display: flex; align-items: center; gap: 16px;
    font-family: "Orbitron", sans-serif;
    font-weight: 700;
    color: var(--navy);
    letter-spacing: 2px;
  }
  .brand__mark {
    width: 34px; height: 34px;
    background: var(--navy);
  }

  /* back */
  .card--back .brand {
    position: absolute; top: 52px; left: 70px;
    font-size: 46px;
  }
  .services {
    position: absolute; left: 0; right: 0; bottom: 0;
    height: 225px;
    background: var(--navy);
    padding: 26px 50px 0;
    box-sizing: border-box;
    font-family: "Orbitron", sans-serif;
    font-weight: 700;
    font-size: 16px;
    letter-spacing: 1.5px;
    color: var(--white);
    text-transform: uppercase;
  }
  .services ul { list-style: none; margin: 0; padding: 0; }
  .services li { line-height: 29px; }
  .bullet {
    display: inline-block; width: 12px; height: 12px;
    background: var(--accent); margin-right: 12px;
  }
  .services__heading { color: var(--accent); font-size: 19px; line-height: 32px; }
  .services__row .bullet { margin-left: 14px; }
  .services__row .bullet:first-child { margin-left: 0; }

  /* front */
  .card--front .brand {
    position: absolute; top: 50px; left: 150px;
    font-size: 68px;
  }
  .card--front .brand__mark { width: 48px; height: 48px; }
  .rule {
    position: absolute; left: 0; right: 0; top: 166px;
    height: 3px; background: var(--navy-dark);
  }
  .nameplate {
    position: absolute; left: 0; right: 0; top: 169px;
    height: 70px; background: var(--white);
  }
  .person {
    position: absolute; left: 250px; top: 178px;
    font-family: "Orbitron", sans-serif; font-weight: 700;
  }
  .person__name { font-size: 28px; color: var(--navy-dark); letter-spacing: 2px; margin: 0; }
  .person__role { font-size: 17px; color: var(--accent); letter-spacing: 1.5px; margin: 2px 0 0 100px; }
  .details {
    position: absolute; left: 0; right: 0; bottom: 0; top: 239px;
    background: var(--navy);
    font-family: "Poppins", sans-serif;
    color: var(--white);
  }
  .contact {
    position: absolute; left: 50px; top: 42px;
    list-style: none; margin: 0; padding: 0;
    font-size: 21px; line-height: 34px;
  }
  .contact li { display: flex; align-items: center; gap: 14px; }
  .contact svg { width: 20px; height: 20px; }
  .address {
    position: absolute; right: 46px; top: 30px;
    text-align: right; font-size: 20px; line-height: 32px; font-style: normal;
  }
</style>
</head>
<body>
<main class="canvas">

  <section class="card card--back" aria-label="Business card back">
    <div class="brand"><span class="brand__mark"></span>K T Masonry</div>
    <div class="services">
      <ul>
        <li><span class="bullet"></span>Ready mixed concrete</li>
        <li><span class="bullet"></span>Bricks and blocks,</li>
        <li><span class="bullet"></span>Quarry products- gravel, aggregates, sand etc.</li>
        <li><span class="bullet"></span>Cement distributor/retailer of reputable brands.</li>
        <li class="services__heading">Other prefab concrete products</li>
        <li class="services__row"><span class="bullet"></span>Culverts <span class="bullet"></span>Wave breakers <span class="bullet"></span>Concrete retaining blocks etc.</li>
      </ul>
    </div>
  </section>

  <section class="card card--front" aria-label="Business card front">
    <div class="brand"><span class="brand__mark"></span>K T Masonry</div>
    <div class="rule"></div>
    <div class="nameplate"></div>
    <div class="person">
      <p class="person__name">Daniel Whitmore</p>
      <p class="person__role">CEO/Founder</p>
    </div>
    <div class="details">
      <ul class="contact">
        <li>
          <svg viewBox="0 0 24 24" fill="none" stroke="#fff" stroke-width="2"><path d="M5 3h4l2 5-3 2a11 11 0 0 0 6 6l2-3 5 2v4a2 2 0 0 1-2 2A17 17 0 0 1 3 5a2 2 0 0 1 2-2z"/></svg>
          555-302-7148
        </li>
        <li>
          <svg viewBox="0 0 24 24" fill="none" stroke="#fff" stroke-width="2"><rect x="2" y="5" width="20" height="14"/><path d="M2 5l10 8 10-8"/></svg>
          daniel@ktmasonry-mail.com
        </li>
        <li>
          <svg viewBox="0 0 24 24" fill="none" stroke="#fff" stroke-width="2"><circle cx="12" cy="12" r="10"/><path d="M2 12h20M12 2c3 3 3 17 0 20M12 2c-3 3-3 17 0 20"/></svg>
          www.ktmasonry-site.com
        </li>
      </ul>
      <address class="address">18 Harbour Road<br>Suite 2, Point Cruz<br>Honiara</address>
    </div>
  </section>

</main>
</body>
</html>
```